Real Estate Company Looking for Business Card Designs for 3 Executives

Hello!
Thanks so much for considering our project! We are a real estate investment company located in Edmonton, Alberta called Bellhaven Group of Companies. We invest/develop both commercial and residential real estate and are looking to create 3 DOUBLE-SIDED business cards for 3 top executives in the company! (for some reason it won't let us select the double-sided option, but yes, the cards are double sided and would be happy to tip extra)

We have certain guidelines that we want our business cards to for sure follow - the back of the Business card has to be the Black Background Version of the Logo which has already been designed and linked as a file (first file). We want the entire back of the card to simply just be the black background logo. In terms of the front of the card, would like to see a smaller version of the white background logo (linked as the second file) in the top left hand corner - of course, feel free to get creative and we can make revisions together along the way! and Then after that, just text. We want the card to be sharp, clean, easy on the eyes and highly professional looking. We would like the card to include the Full name of the Company (Bellhaven Group of Companies), Name of the Person, Title, Phone, Email. If possible please provide the front part of the card for 3 people:

1) Bellhaven Group of Companies, Liora Quenby, Chief Financial Officer, 780-555-0142, lioraquenby@bellhavengroup.example

2) Bellhaven Group of Companies, Tobias Quenby, Chief Executive Officer, 780-555-0187, tobiasquenby@bellhavengroup.example

3) Bellhaven Group of Companies, Rui Delcourt, Chief Operations Officer, 587-555-0163, ruidelcourt@bellhavengroup.example

Thank you so much for considering our project & we look forward to seeing your designs!

```html
<!DOCTYPE html>
<html lang="en">
<head>
<meta charset="utf-8">
<title>Bellhaven Group of Companies — Business Card</title>
<link rel="stylesheet" href="https://fonts.googleapis.com/css2?family=Montserrat:wght@400;500;600&family=Karla:wght@400;700&display=swap">
<style>
  :root {
    --backdrop: #2a2a2c;
    --ink: #0b0b0b;
    --paper: #f7f7f5;
    --paper-text: #151515;
    --muted-light: #d9d9d9;
    --tree-dark: #050505;
  }
  * { box-sizing: border-box; margin: 0; padding: 0; }
  html, body {
    width: 1200px; height: 874px; overflow: hidden;
    background: var(--backdrop);
  }
  .card {
    position: absolute;
    left: 320px;
    width: 560px; height: 330px;
    box-shadow: 0 14px 30px rgba(0,0,0,.45);
    overflow: hidden;
  }
  /* Back side: logo */
  .card--back { top: 62px; background: var(--paper); }
  .brand {
    position: absolute; left: 0; right: 0; top: 128px;
    display: flex; align-items: center; justify-content: center; gap: 14px;
  }
  .brand__mark { width: 14px; height: 14px; background: var(--ink); }
  .brand__name {
    font-family: "Montserrat", sans-serif; font-weight: 500;
    font-size: 30px; letter-spacing: 10px; color: var(--ink);
  }

  /* Front side: contact */
  .card--front { top: 452px; background: var(--ink); }
  .contact {
    position: absolute; left: 30px; top: 92px; width: 240px;
    color: #fff; font-family: "Karla", sans-serif;
  }
  .contact__name { font-weight: 700; font-size: 20px; letter-spacing: 1.5px; white-space: nowrap; }
  .contact__title { font-size: 11px; color: var(--muted-light); margin-top: 2px; }
  .contact__list { list-style: none; margin-top: 16px; }
  .contact__item {
    display: flex; align-items: center; gap: 7px;
    font-size: 11px; line-height: 19px; white-space: nowrap;
  }
  .contact__item svg { width: 9px; height: 9px; fill: #fff; flex: none; }
  .forest {
    position: absolute; left: 276px; top: 0; width: 128px; height: 330px;
    background: linear-gradient(90deg, var(--tree-dark) 0%, #2b2b2b 18%, var(--tree-dark) 35%, #3a3a3a 55%, var(--tree-dark) 75%, #222 100%);
  }
  .company-panel {
    position: absolute; left: 404px; top: 0; width: 156px; height: 330px;
    background: var(--paper); border-bottom-left-radius: 20px;
  }
  .company-panel__text {
    position: absolute; left: 34px; bottom: 26px; height: 282px;
    writing-mode: vertical-rl; transform: rotate(180deg);
    font-family: "Montserrat", sans-serif; color: var(--paper-text);
    text-align: start; white-space: nowrap;
  }
  .company-panel__name { display: block; font-size: 30px; font-weight: 500; letter-spacing: 1px; line-height: 36px; }
  .company-panel__sub { display: block; font-size: 15px; font-weight: 400; letter-spacing: 1px; line-height: 22px; }
</style>
</head>
<body>
  <section class="card card--back" aria-label="Card back">
    <div class="brand">
      <span class="brand__mark"></span>
      <span class="brand__name">BELLHAVEN</span>
    </div>
  </section>

  <section class="card card--front" aria-label="Card front">
    <div class="contact">
      <p class="contact__name">LIORA QUENBY</p>
      <p class="contact__title">Chief Financial Officer</p>
      <ul class="contact__list">
        <li class="contact__item">
          <svg viewBox="0 0 10 10" aria-hidden="true"><path d="M2 0.5 L3.6 0.5 L4.2 3 L3 3.8 Q4 6 6.2 7 L7 5.8 L9.5 6.4 L9.5 8 Q9.5 9.5 8 9.5 Q0.5 9 0.5 2 Q0.5 0.5 2 0.5Z"/></svg>
          780-555-0142
        </li>
        <li class="contact__item">
          <svg viewBox="0 0 10 10" aria-hidden="true"><path d="M0.5 2 H9.5 V8 H0.5Z M0.5 2 L5 5.5 L9.5 2" stroke="#000" stroke-width=".8"/></svg>
          lioraquenby@bellhavengroup.example
        </li>
        <li class="contact__item">
          <svg viewBox="0 0 10 10" aria-hidden="true"><circle cx="5" cy="5" r="4.5"/><path d="M0.5 5 H9.5 M5 0.5 Q2.5 5 5 9.5 M5 0.5 Q7.5 5 5 9.5" stroke="#000" stroke-width=".7" fill="none"/></svg>
          www.bellhavengroup.example
        </li>
      </ul>
    </div>
    <div class="forest" role="img" aria-label="Tall pine tree silhouettes in black and white"></div>
    <div class="company-panel">
      <p class="company-panel__text">
        <span class="company-panel__name">BELLHAVEN</span>
        <span class="company-panel__sub">GROUP OF COMPANIES</span>
      </p>
    </div>
  </section>
</body>
</html>
```